Letterhead & Greeting Card Design Project

I need a few files prepared for dynamic digital printing: letterhead and 2 postcards with an envelope for each. Enclosed are specific directions from the printer for each file and overall. I have also enclosed mockups of what I would like on those designs and some raw files to work with.

Industry/Entity Type

Digital

```html
<!DOCTYPE html>
<html lang="en">
<head>
<meta charset="utf-8">
<title>Place Card – Jane Doe</title>
<link rel="stylesheet" href="https://fonts.googleapis.com/css2?family=Fira+Sans:wght@400;700&display=swap">
<style>
  :root {
    --brand-blue: #0a9bd0;
    --fold-blue: #a6daee;
    --accent-grey: #666666;
    --ink: #111111;
    --paper: #ffffff;
  }
  html, body {
    margin: 0;
    padding: 0;
    overflow: hidden;
    background: var(--paper);
  }
  .card {
    position: relative;
    width: 826px;
    height: 1200px;
    overflow: hidden;
    background: var(--paper);
    font-family: "Fira Sans", sans-serif;
  }
  .card__frame {
    position: absolute;
    left: 50px;
    top: 50px;
    width: 723px;
    height: 1095px;
    border: 5px solid var(--brand-blue);
    box-sizing: border-box;
    border-radius: 3px;
  }
  .card__fold {
    position: absolute;
    left: 0;
    top: 594px;
    width: 826px;
    height: 0;
    border-top: 1.5px solid var(--fold-blue);
  }
  .sender {
    position: absolute;
    left: 213px;
    top: 62px;
    width: 400px;
    transform: rotate(180deg);
    text-align: center;
    color: var(--ink);
    font-size: 26px;
    font-weight: 400;
    line-height: 43px;
    letter-spacing: 0.5px;
  }
  .sender p { margin: 0; }
  .guest-name {
    position: absolute;
    left: 119px;
    top: 704px;
    margin: 0;
    color: var(--ink);
    font-size: 94px;
    font-weight: 700;
    line-height: 1;
    letter-spacing: -1px;
  }
  .accent-cluster {
    position: absolute;
    left: 528px;
    top: 897px;
    width: 298px;
    height: 303px;
    border-top-left-radius: 40px;
    background: linear-gradient(135deg, var(--accent-grey) 0%, var(--accent-grey) 35%, var(--brand-blue) 70%, var(--brand-blue) 100%);
    opacity: 0.85;
  }
</style>
</head>
<body>
  <main class="card">
    <div class="card__frame"></div>
    <div class="card__fold"></div>

    <section class="sender">
      <p class="sender__name">John Doe</p>
      <p class="sender__company">Company</p>
      <p class="sender__phone">Phone</p>
      <p class="sender__email">Email</p>
    </section>

    <h1 class="guest-name">Jane Doe</h1>

    <div class="accent-cluster" role="img" aria-label="Decorative cluster of grey and blue dots in the lower right corner"></div>
  </main>
</body>
</html>
```